Custom Cabinet Shop Needs a website design

Hi,
We need a website for a Custom Cabinet Shop and Cabinet parts manufacturing business.
The business has two sides to it. One side provides custom Kitchens, vanities, entertainment units, offices and what not to homeowners and contractors.
The 2nd side of the business provides built to order cabinet boxes and other parts required to put together a project to other cabinet shops, small contractors looking to install there own cabinets.
Website will need a Gallery to display work.
Color scheme to go well with logo.
current website is www.brambleoakcustomcabinets.com
being changed to www.brambleoak.ca
Logo Included in attached files.
Tagline "Joinery with Spirit"
Mission Statement "Our passion is to deliver inspired cabinetry solutions to suit all your needs, supported by our phenomenal star class customer service"
The website should convey quality and professionalism.
Thank you.
Homeowners/ Contractors
Entertainment

```html
<!DOCTYPE html>
<html lang="en">
<head>
<meta charset="utf-8">
<title>Brambleoak Custom Cabinets</title>
<link href="https://fonts.googleapis.com/css2?family=Exo+2:ital,wght@0,400;0,600;0,700;1,400&family=Open+Sans:ital,wght@0,400;0,600;0,700;1,400&family=Oswald:wght@600&family=Raleway:wght@500&display=swap" rel="stylesheet">
<style>
:root{
  --orange:#f05a22;
  --orange-dark:#d94c18;
  --charcoal:#3a3a3a;
  --ink:#1e1e1e;
  --black:#0d0d0d;
  --grey:#8a8a8a;
  --light:#e6e6e6;
  --white:#ffffff;
}
*{margin:0;padding:0;box-sizing:border-box}
html,body{width:1200px;height:2507px;overflow:hidden;background:var(--white)}
body{position:relative;font-family:"Open Sans",Arial,sans-serif;color:var(--ink)}
.abs{position:absolute}

/* header */
.top-rule{left:0;top:0;width:1200px;height:7px;background:var(--orange)}
.brand{left:87px;top:40px;display:flex;align-items:center;gap:14px}
.brand-mark{width:52px;height:52px;background:var(--orange)}
.brand-name{font-family:"Exo 2",sans-serif;font-weight:700;font-size:34px;color:var(--ink);letter-spacing:1px;text-transform:uppercase}
.social-top{right:85px;top:8px;display:flex;gap:5px}
.social-top span{width:34px;height:37px;background:var(--orange);display:block}
.perks{left:660px;top:72px;display:flex;gap:22px;font-family:"Exo 2",sans-serif;font-size:12.5px;color:var(--grey);line-height:15px}
.perk{display:flex;align-items:center;gap:8px;padding-right:20px;border-right:1px solid var(--light)}
.perk:last-child{border:0;padding-right:0}
.perk svg{flex:none}

/* nav */
.navbar{left:0;top:147px;width:1200px;height:82px;background:var(--charcoal)}
.search{left:92px;top:164px;width:264px;height:45px;background:var(--white);border-radius:3px;font-size:12px;color:#666;padding:14px 16px}
.search svg{position:absolute;right:16px;top:14px}
.nav-tab{left:393px;top:139px;width:707px;height:90px;background:var(--orange);border-radius:6px 6px 0 0}
.nav{left:393px;top:147px;width:707px;height:82px;display:flex;font-family:"Exo 2",sans-serif;font-weight:600;font-size:15.5px;color:var(--white)}
.nav a{flex:1;display:flex;align-items:center;justify-content:center;color:inherit;text-decoration:none;border-right:1px solid rgba(0,0,0,.12)}
.nav a:last-child{border-right:0}

/* hero */
.hero{left:0;top:229px;width:1200px;height:638px;background:linear-gradient(180deg,#cfd3d0 0%,#b8a48a 40%,#6b4e36 75%,#3e2c20 100%)}
.hero-title{left:87px;top:495px;font-family:"Oswald",sans-serif;font-weight:600;font-size:58px;color:var(--white);text-transform:uppercase;letter-spacing:-.5px;text-shadow:0 2px 6px rgba(0,0,0,.45)}
.hero-arrow{top:810px;width:30px;height:57px;background:var(--orange)}
.hero-arrow.left{left:0;border-radius:0 30px 0 0}
.hero-arrow.right{right:0;border-radius:30px 0 0 0}
.hero-dots{left:520px;top:845px;width:140px;height:22px;background:var(--orange);border-radius:14px 14px 0 0;display:flex;justify-content:center;align-items:center;gap:7px}
.hero-dots i{width:9px;height:9px;border-radius:50%;background:var(--white);display:block}
.hero-dots i.on{background:var(--ink)}

/* welcome */
.welcome{left:0;top:867px;width:1200px;height:149px;background:var(--orange);color:var(--white)}
.welcome h1{position:absolute;left:87px;top:36px;font-family:"Exo 2",sans-serif;font-weight:600;font-size:25px}
.welcome p{position:absolute;left:87px;top:72px;width:680px;font-size:15.5px;line-height:25px}
.welcome svg{position:absolute;left:765px;top:38px}
.btn-dark{position:absolute;left:877px;top:47px;width:197px;height:62px;background:#222;border-radius:3px;color:var(--white);font-family:"Exo 2",sans-serif;font-size:16.5px;display:flex;align-items:center;justify-content:center}

/* section titles */
.section-head{left:85px;top:1054px;width:1028px;display:flex;align-items:center;gap:18px}
.section-head h2{font-family:"Raleway",sans-serif;font-weight:500;font-size:32px;color:var(--ink)}
.section-head .rule{flex:1;height:1px;background:#cfcfcf}

/* services */
.services{left:85px;top:1120px;width:1028px;height:247px;display:flex;border:1px solid #ddd}
.svc{width:237px;padding:28px 16px 0 17px;color:var(--white);position:relative}
.svc.res{background:var(--orange)}
.svc.biz{background:#222;width:235px}
.svc h3{font-family:"Exo 2",sans-serif;font-weight:600;font-size:21px;margin-bottom:18px}
.svc p{font-style:italic;font-size:12.5px;line-height:25px}
.svc .more{position:absolute;right:12px;bottom:24px;font-style:italic;font-size:12px}
.svc-photo{height:100%;position:relative}
.svc-photo.a{width:253px;background:linear-gradient(160deg,#d9d4c8,#7b6a5a 55%,#3b2d26)}
.svc-photo.b{flex:1;background:linear-gradient(170deg,#e8e6e2,#9a9590 45%,#2f3438)}
.quick{position:absolute;left:33px;top:94px;width:170px;height:40px;background:rgba(30,30,30,.8);color:var(--white);font-size:13px;display:flex;align-items:center;justify-content:center;gap:9px}

/* gallery */
.gallery{left:0;top:1425px;width:1200px;height:458px;background:linear-gradient(180deg,#2a2826,#161514 60%,#211e1c)}
.gallery h2{position:absolute;left:0;width:1200px;top:41px;text-align:center;font-family:"Raleway",sans-serif;font-weight:500;font-size:31px;color:var(--white)}
.card{position:absolute;top:114px;width:316px;height:244px}
.card .ph{height:201px}
.card .cap{height:43px;background:var(--orange);color:var(--white);font-family:"Exo 2",sans-serif;font-weight:600;font-size:17.5px;display:flex;align-items:center;justify-content:space-between;padding:0 15px 0 12px}
.g-dots{position:absolute;left:549px;top:402px;display:flex;gap:7px}
.g-dots i{width:12px;height:12px;background:var(--white);transform:rotate(45deg);display:block}
.g-dots i.on{background:var(--orange)}

/* testimonials */
.t-head{left:85px;top:1918px;width:1028px;display:flex;align-items:center;gap:14px}
.t-head h2{font-family:"Exo 2",sans-serif;font-weight:600;font-size:25px;color:var(--orange)}
.t-head .rule{flex:1;height:1px;background:#e3e3e3}
.quote{position:absolute;top:1992px;width:470px}
.avatar{position:absolute;left:0;top:0;width:126px;height:113px;border-radius:50%;border:5px solid #eee;background:linear-gradient(180deg,#d8c2ac,#b9d0e2)}
.quote h4{position:absolute;left:159px;top:5px;font-family:"Exo 2",sans-serif;font-weight:600;font-size:14px;color:var(--ink)}
.quote p{position:absolute;left:159px;top:38px;width:318px;font-size:12px;line-height:19px;color:#777}

/* footer */
.footer{left:0;top:2151px;width:1200px;height:272px;background:var(--orange);color:var(--white)}
.footer h5{font-family:"Exo 2",sans-serif;font-weight:500;font-size:18.5px;position:absolute;top:34px}
.f-col{position:absolute;font-size:12.5px;line-height:23px}
.f-item{display:flex;gap:14px;margin-bottom:17px}
.f-item svg{flex:none;margin-top:4px}
.divider{position:absolute;top:20px;width:2px;height:230px;background:linear-gradient(180deg,transparent,rgba(0,0,0,.2),transparent)}
.signup{position:absolute;left:784px;top:103px;display:flex}
.signup .field{width:239px;height:44px;background:var(--white);color:#999;font-size:12.5px;padding:13px 16px}
.signup .go{width:90px;height:44px;background:var(--black);color:var(--white);font-size:17px;display:flex;align-items:center;justify-content:center}

.bottom{left:0;top:2423px;width:1200px;height:84px;background:var(--black)}
.bottom p{position:absolute;left:85px;top:32px;color:var(--white);font-family:"Exo 2",sans-serif;font-weight:600;font-size:12px}
.social-foot{position:absolute;right:82px;top:24px;display:flex;gap:22px}
.social-foot span{width:33px;height:33px;background:#3d3d3d;display:block}
</style>
</head>
<body>

<div class="abs top-rule"></div>

<header>
  <div class="abs brand">
    <span class="brand-mark"></span>
    <span class="brand-name">Brambleoak</span>
  </div>
  <div class="abs social-top" aria-label="Social links"><span></span><span></span><span></span><span></span></div>
  <div class="abs perks">
    <div class="perk">
      <svg width="40" height="26" viewBox="0 0 40 26" fill="none" stroke="#9a9a9a" stroke-width="2"><rect x="2" y="4" width="22" height="14"/><path d="M24 8h8l6 6v4H24"/><circle cx="9" cy="21" r="3"/><circle cx="31" cy="21" r="3"/></svg>
      <span>Free Shipping<br>On all Products</span>
    </div>
    <div class="perk">
      <svg width="34" height="30" viewBox="0 0 34 30" fill="#9a9a9a"><rect x="10" y="2" width="16" height="12" rx="2"/><path d="M2 20h10l8 3 10-5 2 3-12 7H2z"/></svg>
      <span>Money Back<br>Guarantee</span>
    </div>
    <div class="perk">
      <svg width="26" height="28" viewBox="0 0 26 28" fill="none" stroke="#9a9a9a" stroke-width="2"><rect x="2" y="9" width="22" height="7"/><rect x="4" y="16" width="18" height="10"/><path d="M13 9v17M13 9c-3-6-9-6-7 0M13 9c3-6 9-6 7 0"/></svg>
      <span>Specoal weekly<br>Offer</span>
    </div>
  </div>
</header>

<div class="abs navbar"></div>
<div class="abs search">Search...
  <svg width="16" height="16" viewBox="0 0 16 16" fill="none" stroke="#222" stroke-width="2"><circle cx="6.5" cy="6.5" r="5"/><path d="M10.5 10.5 15 15"/></svg>
</div>
<div class="abs nav-tab"></div>
<nav class="abs nav">
  <a href="#">Home</a><a href="#">Gallery</a><a href="#">Services</a><a href="#">Warranty</a><a href="#">Contact</a>
</nav>

<section>
  <div class="abs hero" role="img" aria-label="Photo of a sunlit dining nook with a rustic wooden table, bench and cushioned seating"></div>
  <div class="abs hero-title">Joinery with Spirit</div>
  <div class="abs hero-arrow left"><svg width="30" height="57" viewBox="0 0 30 57"><path d="M17 27l-7 7 7 7" fill="none" stroke="#fff" stroke-width="3"/></svg></div>
  <div class="abs hero-arrow right"><svg width="30" height="57" viewBox="0 0 30 57"><path d="M13 27l7 7-7 7" fill="none" stroke="#fff" stroke-width="3"/></svg></div>
  <div class="abs hero-dots"><i class="on"></i><i></i><i></i></div>
</section>

<section class="abs welcome">
  <h1>WELCOME TO BRAMBLEOAK CUSTOM CABINETS</h1>
  <p>Our passion is to deliver inspired cabinetry solutions to suit all your needs, supported by our phenomenal star class customer service</p>
  <svg width="50" height="74" viewBox="0 0 50 74" fill="none" stroke="#fff" stroke-width="4" stroke-linecap="round"><path d="M4 4c14 0 16 8 16 18s4 15 24 15C24 37 20 42 20 52S18 70 4 70"/></svg>
  <div class="btn-dark">READ MORE</div>
</section>

<div class="abs section-head">
  <h2>Services</h2><span class="rule"></span>
  <svg width="30" height="16" viewBox="0 0 30 16" fill="none" stroke-width="3"><path d="M10 2 4 8l6 6" stroke="#111"/><path d="M20 2l6 6-6 6" stroke="#f05a22"/></svg>
</div>
<section class="abs services">
  <div class="svc res">
    <h3>Residential</h3>
    <p>Celebrating its 11th year in design, Harbourline Interior Design has grown exponentially as an interior design company providing design solutions for</p>
    <span class="more">- Read More +</span>
  </div>
  <div class="svc-photo a" role="img" aria-label="Photo of a modern bathroom vanity with under-cabinet lighting">
    <div class="quick"><svg width="18" height="12" viewBox="0 0 18 12"><path d="M1 6c4-7 12-7 16 0-4 7-12 7-16 0z" fill="#fff"/><circle cx="9" cy="6" r="2.5" fill="#222"/></svg>Quick View</div>
  </div>
  <div class="svc biz">
    <h3>Business</h3>
    <p>Celebrating its 11th year in design, Harbourline Interior Design has grown exponentially as an interior design company providing design solutions for</p>
    <span class="more">- Read More +</span>
  </div>
  <div class="svc-photo b" role="img" aria-label="Photo of a bright kitchen with a large island and pendant lights"></div>
</section>

<section class="abs gallery" role="region" aria-label="Gallery">
  <h2>Gallery</h2>
  <div class="card" style="left:85px"><div class="ph" role="img" aria-label="Photo of a wooden entertainment unit with a wall-mounted television" style="background:linear-gradient(180deg,#cfc6c4,#6a3f2c 70%,#3a2118)"></div><div class="cap">Lorem Ipsum dollar<svg width="18" height="18" viewBox="0 0 18 18"><circle cx="9" cy="9" r="9" fill="#fff"/><path d="M9 4v10M4 9h10" stroke="#f05a22" stroke-width="2.4"/></svg></div></div>
  <div class="card" style="left:441px"><div class="ph" role="img" aria-label="Photo of an open kitchen with white cabinets and stainless appliances" style="background:linear-gradient(180deg,#e9e6df,#8f8578 55%,#3a3430)"></div><div class="cap">Lorem Ipsum dollar<svg width="18" height="18" viewBox="0 0 18 18"><circle cx="9" cy="9" r="9" fill="#fff"/><path d="M9 4v10M4 9h10" stroke="#f05a22" stroke-width="2.4"/></svg></div></div>
  <div class="card" style="left:800px"><div class="ph" role="img" aria-label="Photo of a dark wood kitchen with an island and bar seating" style="background:linear-gradient(180deg,#6d625a,#3c302a 55%,#7a5a3c)"></div><div class="cap">Lorem Ipsum dollar<svg width="18" height="18" viewBox="0 0 18 18"><circle cx="9" cy="9" r="9" fill="#fff"/><path d="M9 4v10M4 9h10" stroke="#f05a22" stroke-width="2.4"/></svg></div></div>
  <div class="g-dots"><i class="on"></i><i></i><i></i></div>
</section>

<div class="abs t-head"><h2>Testimonials</h2><span class="rule"></span></div>
<div class="quote" style="left:88px">
  <div class="avatar" role="img" aria-label="Portrait photo of a client"></div>
  <h4>ORGANIZATIONAL CAPACITY</h4>
  <p>Nulla sollicitudin tincidunt dui et egestas. Phasellus non sem tum, ullamcorper vitae, accumsan dui. Duis dignissim condi lorem. Maecenas facilisis ipsum sed porttitor rutrum. Nulla sollicitudin tincidunt</p>
</div>
<div class="quote" style="left:628px">
  <div class="avatar" role="img" aria-label="Portrait photo of a client"></div>
  <h4>STRATEGIC NETWORKS</h4>
  <p>Nulla sollicitudin tincidunt dui et egestas. Phasellus non sem tum, ullamcorper vitae, accumsan dui. Duis dignissim condi lorem. Maecenas facilisis ipsum sed porttitor rutrum. Nulla sollicitudin tincidunt</p>
</div>

<footer class="abs footer">
  <h5 style="left:84px">CONTACT US</h5>
  <div class="f-col" style="left:84px;top:76px;width:270px">
    <div class="f-item"><svg width="22" height="22" viewBox="0 0 22 22" fill="#fff"><rect x="10" y="1" width="2" height="20"/><path d="M12 3h8l2 3-2 3h-8zM10 9H3l-2 3 2 3h7z"/></svg><span>Fernway Cabinet Works Ltd. 2740 Larkspur Avenue Kelvale, B.C. V0X 1A0</span></div>
    <div class="f-item"><svg width="22" height="16" viewBox="0 0 22 16" fill="#fff"><path d="M5 1l3 4-2 2c1 3 3 5 6 6l2-2 4 3-2 2C9 16 2 9 3 3z"/></svg><span>Phone:(555) 014-2280</span></div>
    <div class="f-item"><svg width="22" height="16" viewBox="0 0 22 16" fill="#fff"><rect x="4" y="0" width="10" height="5"/><rect x="1" y="5" width="16" height="8" rx="2"/><rect x="4" y="10" width="10" height="6"/></svg><span>Fax:(555) 014-2281</span></div>
  </div>
  <div class="divider" style="left:400px"></div>
  <h5 style="left:434px">LATEST TWEET'S</h5>
  <div class="f-col" style="left:434px;top:76px;width:280px">
    <div class="f-item"><svg width="22" height="22" viewBox="0 0 22 22"><rect width="22" height="22" rx="4" fill="#fff"/><path d="M6 8l5 4 5-4" stroke="#f05a22" stroke-width="2" fill="none"/></svg><span>Good morning .... wherever you are today! All of us at ...See more here http://t.co/Bk4rQw7Lmz</span></div>
    <div class="f-item"><svg width="22" height="22" viewBox="0 0 22 22"><rect width="22" height="22" rx="4" fill="#fff"/><path d="M6 8l5 4 5-4" stroke="#f05a22" stroke-width="2" fill="none"/></svg><span>Good morning .... wherever you are today! All of us at ...See more here http://t.co/Bk4rQw7Lmz</span></div>
  </div>
  <div class="divider" style="left:744px"></div>
  <h5 style="left:782px;top:42px">NEWSLETTER</h5>
  <div class="f-col" style="left:782px;top:72px">Excepteur sint occaecat cupidatat non proident,</div>
  <div class="signup"><div class="field">Enter your email address</div><div class="go">Sign Up</div></div>
</footer>

<div class="abs bottom">
  <p>COPYRIGHT © 2015 BRAMBLEOAK. ALL RIGHTS RESERVED.</p>
  <div class="social-foot" aria-label="Social links"><span></span><span></span><span></span><span></span></div>
</div>

</body>
</html>
```